Halvor Grading and Septic needs a flyer to submit to contractors to offer our services

I need a sleek profession one page full color high gloss document showcasing our services to give to Mobile Home Companies and contractors that need our services.

Target Market(s)

Home Builders. Mobile Home Salesmen. People Building new homes.

Industry/Entity Type

Construction

Font styles to use
Serif
Sans Serif

Requirements
Must have
• Phone Number. Email address. Logo. Services offered: Mobile Home Pads, Meter Pole Placement and Connection, Waterline Connection, On Site Septic System Installs
Should not have
• Jokes, Nothing trying to be cute

```html
<!DOCTYPE html>
<html lang="en">
<head>
<meta charset="utf-8">
<title>Halvor Grading and Septic – Flyer</title>
<link href="https://fonts.googleapis.com/css2?family=Montserrat:ital,wght@0,500;0,600;0,700;0,800;1,500;1,600;1,700;1,800;1,900&display=swap" rel="stylesheet">
<style>
  :root{
    --brand-blue:#1c4f87;
    --brand-blue-dark:#163f6d;
    --brand-red:#c8202a;
    --white:#ffffff;
    --soil:#8a6a4a;
    --map-bg:#eef0e2;
  }
  *{box-sizing:border-box;margin:0;padding:0}
  html,body{width:803px;height:1200px;overflow:hidden;background:#e6e6e6}
  .flyer{position:relative;width:803px;height:1200px;background:var(--brand-blue);font-family:"Montserrat",sans-serif;color:var(--white);overflow:hidden}
  .flyer-shapes{position:absolute;inset:0}
  .brand{position:absolute;left:52px;top:62px;width:270px;display:flex;align-items:center;gap:10px}
  .brand-mark{width:22px;height:22px;background:var(--brand-blue);flex:none}
  .brand-name{font-weight:800;font-size:21px;line-height:1.1;color:var(--brand-blue);text-transform:uppercase}
  .headline{position:absolute;left:0;width:803px;text-align:center;font-style:italic;font-weight:900;text-transform:uppercase;line-height:1}
  .headline-top{top:214px;font-size:42px;left:-8px}
  .headline-main{top:256px;font-size:70px;color:var(--brand-red);left:10px;letter-spacing:1px}
  .headline-bottom{top:328px;font-size:52px;left:-8px}
  .intro{position:absolute;left:120px;width:520px;top:420px;text-align:center;font-style:italic;font-weight:600;font-size:14.5px;line-height:1.25}
  .intro-cta{position:absolute;left:120px;width:520px;top:470px;text-align:center;font-style:italic;font-weight:600;font-size:21px}
  .pill{position:absolute;top:575px;height:29px;width:264px;border-radius:15px;background:var(--brand-red);text-align:center;font-style:italic;font-weight:800;font-size:21px;line-height:29px}
  .pill-services{left:73px}
  .pill-area{left:458px}
  .service{position:absolute;width:190px;text-align:center}
  .service-icon{display:block;margin:0 auto;width:86px;height:86px}
  .service-label{display:block;margin-top:6px;font-weight:600;font-size:12.5px;line-height:1.2;text-transform:uppercase}
  .service-pads{left:22px;top:626px}
  .service-meter{left:197px;top:626px}
  .service-water{left:24px;top:767px}
  .service-septic{left:197px;top:767px}
  .service-area-map{position:absolute;left:435px;top:645px;width:310px;height:244px;background:linear-gradient(135deg,#f1efe4,#e3ecd6 60%,#d9e6cf);border:1px solid #cfd6c2}
  .contact-email{position:absolute;left:20px;width:440px;top:1128px;text-align:center;font-style:italic;font-weight:700;font-size:17.5px}
  .contact-phone{position:absolute;left:470px;width:320px;top:1114px;text-align:center;font-weight:800;font-size:34px}
</style>
</head>
<body>
<main class="flyer">
  <svg class="flyer-shapes" width="803" height="1200" viewBox="0 0 803 1200" aria-hidden="false">
    <defs>
      <linearGradient id="site-photo" x1="0" y1="0" x2="1" y2="1">
        <stop offset="0" stop-color="#6f7b72"/>
        <stop offset="0.45" stop-color="#a48f72"/>
        <stop offset="1" stop-color="#7c8a86"/>
      </linearGradient>
      <linearGradient id="photo-shade" x1="0" y1="0" x2="0" y2="1">
        <stop offset="0" stop-color="#1c4f87" stop-opacity="0.05"/>
        <stop offset="1" stop-color="#1c4f87" stop-opacity="0.5"/>
      </linearGradient>
      <linearGradient id="thumb-photo" x1="0" y1="0" x2="0" y2="1">
        <stop offset="0" stop-color="#9ea3a0"/>
        <stop offset="0.45" stop-color="#8a5a40"/>
        <stop offset="1" stop-color="#7a4a34"/>
      </linearGradient>
    </defs>

    <!-- header white -->
    <rect class="header-bg" x="0" y="0" width="803" height="170" fill="var(--white)"/>
    <rect x="0" y="0" width="803" height="22" fill="var(--white)"/>

    <!-- hero photo area -->
    <g role="img" aria-label="Photo of an excavator beside freshly dug soil and newly installed septic tank lids">
      <path d="M380 56 H803 V408 H0 V168 H300 Z" fill="url(#site-photo)"/>
      <path d="M380 56 H803 V408 H0 V168 H300 Z" fill="url(#photo-shade)"/>
      <path d="M134 408 H651 L626 513 H112 Z" fill="#5f7390" opacity="0.85"/>
    </g>
    <path d="M803 46 H372 L292 158 H0" fill="none" stroke="var(--brand-blue)" stroke-width="8"/>
    <path d="M803 33 H365 L285 140" fill="none" stroke="var(--brand-blue)" stroke-width="3"/>
    <path d="M0 408 H134 L112 513 H626 L651 408 H803" fill="none" stroke="var(--white)" stroke-width="4"/>

    <!-- column divider -->
    <line x1="403" y1="553" x2="403" y2="889" stroke="#6d8db3" stroke-width="1.5"/>

    <!-- work photos -->
    <g fill="url(#thumb-photo)" stroke="var(--brand-red)" stroke-width="3">
      <path role="img" aria-label="Photo of a finished septic install" d="M81 921 H230 L222 1016 H73 Z"/>
      <path role="img" aria-label="Photo of a mobile home pad" d="M250 921 H399 L391 1016 H242 Z"/>
      <path role="img" aria-label="Photo of septic tank lids in fresh soil" d="M419 921 H568 L560 1016 H411 Z"/>
      <path role="img" aria-label="Photo of a completed home site" d="M588 921 H744 L736 1016 H580 Z"/>
    </g>

    <!-- footer -->
    <path d="M0 1059 H496 L466 1200 H0 Z" fill="var(--brand-red)"/>
    <path d="M0 1056 H500 L470 1200" fill="none" stroke="var(--white)" stroke-width="5"/>
    <rect x="466" y="1184" width="337" height="16" fill="var(--brand-red)"/>

    <!-- email icon -->
    <circle cx="256" cy="1099" r="20" fill="var(--white)"/>
    <rect x="245" y="1091" width="22" height="16" rx="2" fill="none" stroke="var(--brand-red)" stroke-width="2.5"/>
    <path d="M245 1092 L256 1101 L267 1092" fill="none" stroke="var(--brand-red)" stroke-width="2.5"/>

    <!-- phone icon -->
    <path d="M632 1069 c-3 3 -2 9 4 15 c6 6 12 7 15 4 l2 -2 l-5 -5 l-3 2 c-2 -1 -5 -4 -6 -6 l2 -3 l-5 -5 z" fill="var(--white)"/>
    <path d="M641 1068 a9 9 0 0 1 9 9 M641 1063 a14 14 0 0 1 14 14" fill="none" stroke="var(--white)" stroke-width="2"/>
  </svg>

  <div class="brand">
    <span class="brand-mark"></span>
    <span class="brand-name">Halvor Grading<br>&amp; Septic</span>
  </div>

  <h1>
    <span class="headline headline-top">Professional</span>
    <span class="headline headline-main">Wastewater</span>
    <span class="headline headline-bottom">Management</span>
  </h1>

  <p class="intro">Halvor Grading and Septic offers professional septic and excavation services in East Texas.</p>
  <p class="intro-cta">Call us now for a free estimate!</p>

  <h2 class="pill pill-services">Services offered:</h2>
  <h2 class="pill pill-area">Service Area</h2>

  <div class="service service-pads">
    <svg class="service-icon" viewBox="0 0 86 86">
      <circle cx="43" cy="43" r="39" fill="var(--brand-blue)" stroke="var(--brand-red)" stroke-width="5"/>
      <circle cx="43" cy="43" r="33" fill="none" stroke="var(--white)" stroke-width="2.5"/>
      <path d="M24 36 L43 25 L62 36 V54 H24 Z" fill="none" stroke="var(--white)" stroke-width="3"/>
      <rect x="30" y="39" width="10" height="8" fill="var(--white)"/>
      <rect x="46" y="39" width="9" height="15" fill="var(--white)"/>
      <circle cx="31" cy="58" r="3" fill="var(--white)"/><circle cx="39" cy="58" r="3" fill="var(--white)"/>
    </svg>
    <span class="service-label">Mobile<br>Home Pads</span>
  </div>

  <div class="service service-meter">
    <svg class="service-icon" viewBox="0 0 86 86">
      <circle cx="43" cy="43" r="39" fill="var(--brand-blue)" stroke="var(--brand-red)" stroke-width="5"/>
      <circle cx="43" cy="43" r="33" fill="none" stroke="var(--white)" stroke-width="2.5"/>
      <path d="M34 22 V58 M24 26 H44 M26 32 H42" stroke="var(--white)" stroke-width="3" fill="none"/>
      <rect x="44" y="42" width="18" height="16" rx="2" fill="none" stroke="var(--white)" stroke-width="3"/>
      <circle cx="50" cy="50" r="3" fill="var(--white)"/>
      <path d="M50 30 a8 8 0 0 1 8 8" stroke="var(--white)" stroke-width="2.5" fill="none"/>
    </svg>
    <span class="service-label">Meter Pole Placement<br>and Connection</span>
  </div>

  <div class="service service-water">
    <svg class="service-icon" viewBox="0 0 86 86">
      <circle cx="43" cy="43" r="39" fill="var(--brand-blue)" stroke="var(--brand-red)" stroke-width="5"/>
      <circle cx="43" cy="43" r="33" fill="none" stroke="var(--white)" stroke-width="2.5"/>
      <path d="M32 24 H54 V32 H47 V44 H58 V52 H28 V44 H39 V32 H32 Z" fill="var(--white)"/>
      <path d="M30 58 H56 M36 58 V64 M50 58 V64" stroke="var(--white)" stroke-width="3"/>
    </svg>
    <span class="service-label">Waterline<br>Connection</span>
  </div>

  <div class="service service-septic">
    <svg class="service-icon" viewBox="0 0 86 86">
      <circle cx="43" cy="43" r="39" fill="var(--brand-blue)" stroke="var(--brand-red)" stroke-width="5"/>
      <circle cx="43" cy="43" r="33" fill="none" stroke="var(--white)" stroke-width="2.5"/>
      <rect x="32" y="24" width="8" height="7" fill="var(--white)"/><rect x="46" y="24" width="8" height="7" fill="var(--white)"/>
      <path d="M24 36 H62 V58 H24 Z" fill="var(--white)"/>
      <rect x="40" y="44" width="6" height="14" fill="var(--brand-blue)"/>
    </svg>
    <span class="service-label">On Site Septic<br>System Installs</span>
  </div>

  <div class="service-area-map" role="img" aria-label="Map of the East Texas service area with a circle marking the coverage radius"></div>

  <p class="contact-email">office@halvorgradingseptic.com</p>
  <p class="contact-phone">(555) 214-0870</p>
</main>
</body>
</html>
```